Meridale Bed Company Needs Business Card

Looking for a very nice looking business card. Creative but not extravagant. We sell beds and pillows across the U.S. and need something professional but catchy. I have attached the logo.

Name : Devin Holt
Title : President
Phone : (800) 471-2960
Email: sleep@quilmora.com
Website: www.quilmora.com

Can be single-sided or double-sided
horizontal or vertical

Can use Blues/Greys

Target Market(s)

Mass Market

Industry/Entity Type

Retail

Contact Information for Business Card

Name : Devin Holt
Title : President
Phone : (800) 471-2960
Email: sleep@quilmora.com
Website: www.quilmora.com

Requirements
Must have
• Clean, Modern, Smooth
• Can use Blues/Greys
• On the other side without the information - have something simple like www.quilmora.com or our logo
Nice to have
• Surprise me
Should not have
• Nothing crazy, nothing cluttered

```html
<!DOCTYPE html>
<html lang="en">
<head>
<meta charset="utf-8">
<title>Quilmora Business Card</title>
<link rel="stylesheet" href="https://fonts.googleapis.com/css2?family=Nunito+Sans:wght@300;400;600;700&display=swap">
<style>
  :root {
    --backdrop: #414143;
    --card: #262626;
    --accent: #34a3d3;
    --ink: #ffffff;
  }
  * { margin: 0; padding: 0; box-sizing: border-box; }
  html, body {
    width: 1200px;
    height: 1200px;
    overflow: hidden;
    background: var(--backdrop);
    font-family: "Nunito Sans", "Helvetica Neue", Arial, sans-serif;
    color: var(--ink);
  }
  .canvas { position: relative; width: 1200px; height: 1200px; }

  .card {
    position: absolute;
    left: 212px;
    width: 776px;
    height: 431px;
    background: var(--card);
  }
  .card--front { top: 113px; }
  .card--back { top: 656px; }

  .accent-band {
    position: absolute;
    top: 0; right: 0;
    width: 167px;
    height: 100%;
    background: var(--accent);
  }

  .person { position: absolute; left: 45px; top: 44px; }
  .person__name {
    font-size: 34px;
    font-weight: 300;
    line-height: 1;
    letter-spacing: 0.2px;
  }
  .person__name strong { font-weight: 700; }
  .person__title {
    margin: 8px 0 0 40px;
    font-size: 19px;
    font-weight: 400;
    letter-spacing: 0.5px;
  }

  .contacts {
    position: absolute;
    left: 60px;
    top: 182px;
    list-style: none;
  }
  .contacts__item {
    display: flex;
    align-items: center;
    height: 36px;
    margin-bottom: 39px;
    font-size: 20px;
    font-weight: 400;
  }
  .contacts__icon {
    width: 34px;
    height: 34px;
    margin-right: 24px;
    flex: none;
  }

  .brand-name {
    position: absolute;
    left: 0;
    right: 0;
    top: 180px;
    text-align: center;
    font-size: 76px;
    font-weight: 600;
    line-height: 1;
    letter-spacing: 1px;
    color: var(--accent);
  }

  .web-bar {
    position: absolute;
    left: 146px;
    bottom: 0;
    width: 484px;
    height: 47px;
    background: var(--accent);
    display: flex;
    align-items: center;
    justify-content: center;
    font-size: 30px;
    font-weight: 600;
    letter-spacing: 0.5px;
  }
</style>
</head>
<body>
<main class="canvas">

  <section class="card card--front" aria-label="Business card front">
    <div class="person">
      <h1 class="person__name">Devin <strong>Holt</strong></h1>
      <p class="person__title">PRESIDENT</p>
    </div>

    <ul class="contacts">
      <li class="contacts__item">
        <svg class="contacts__icon" viewBox="0 0 24 24" aria-hidden="true">
          <path fill="#34a3d3" d="M6.6 10.8c1.4 2.8 3.8 5.1 6.6 6.6l2.2-2.2c.3-.3.7-.4 1-.2 1.1.4 2.3.6 3.6.6.6 0 1 .4 1 1V20c0 .6-.4 1-1 1C10.6 21 3 13.4 3 4c0-.6.4-1 1-1h3.5c.6 0 1 .4 1 1 0 1.3.2 2.5.6 3.6.1.3 0 .7-.2 1z"/>
        </svg>
        <span>(800) 471-2960</span>
      </li>
      <li class="contacts__item">
        <svg class="contacts__icon" viewBox="0 0 24 24" aria-hidden="true">
          <rect x="1.5" y="5" width="21" height="14" fill="#34a3d3"/>
          <path d="M1.5 5l10.5 8 10.5-8M1.5 19l8-7M22.5 19l-8-7" fill="none" stroke="#262626" stroke-width="1.3"/>
        </svg>
        <span>sleep@quilmora.com</span>
      </li>
      <li class="contacts__item">
        <svg class="contacts__icon" viewBox="0 0 24 24" aria-hidden="true">
          <g fill="none" stroke="#34a3d3" stroke-width="1.8">
            <circle cx="12" cy="12" r="10"/>
            <ellipse cx="12" cy="12" rx="4.5" ry="10"/>
            <path d="M2 12h20M12 2v20M3.8 7h16.4M3.8 17h16.4"/>
          </g>
        </svg>
        <span>www.quilmora.com</span>
      </li>
    </ul>

    <div class="accent-band"></div>
  </section>

  <section class="card card--back" aria-label="Business card back">
    <p class="brand-name">quilmora</p>
    <div class="web-bar">www.quilmora.com</div>
  </section>

</main>
</body>
</html>
```